Ledgerwise Forge - WordPress Theme & Logo

Design a logo and Wordpress website design for Ledgerwise Forge. Ledgerwise Forge provides cryptocurrency development services to clients who need a team to create & continue developing a new cryptocurrency or who want to replace their current cryptocurrency development team. more details in the attached document.
Updates

Target Market(s)

Entrepreneurs who are building a business / platform that makes use of an underlying cryptocurrency.

Logo Text

LF or Ledgerwise Forge

Coding

Coded - Design and coding required

Font styles to use
Sans Serif

Requirements
Must have
• Professional logo, complete coded Wordpress theme for all pages, containing all specified links and buttons
Nice to have
• It would be nice if the buttons that are meant to integrate with Dealtrail contain the necessary code for that. I can provide any necessary Dealtrail details from my account.
Should not have
• Slow loading time

```html
<!DOCTYPE html>
<html lang="en">
<head>
<meta charset="utf-8">
<title>Ledgerwise Forge</title>
<link href="https://fonts.googleapis.com/css2?family=Roboto:wght@400;500;700;900&family=Raleway:wght@400;500;600&display=swap" rel="stylesheet">
<style>
:root{
  --blue:#0d5cad;
  --blue-dark:#0a4a8f;
  --navy:#07142b;
  --ink:#111;
  --text:#333;
  --muted:#8a8f99;
  --light:#eef4fb;
  --white:#fff;
}
*{box-sizing:border-box;margin:0;padding:0}
html,body{width:1200px;height:4026px;overflow:hidden}
body{font-family:"Raleway",sans-serif;color:var(--text);background:var(--white);position:relative}
.abs{position:absolute}
h1,h2,h3,.nav,.btn{font-family:"Roboto",sans-serif}
.center{text-align:center;left:0;width:1200px}
.bar{width:60px;height:3px;background:var(--blue);margin:14px auto 0}
.btn{display:inline-flex;align-items:center;gap:10px;background:var(--blue);color:#fff;font-weight:700;font-size:15px;padding:0 20px;height:45px;border-radius:3px;text-transform:uppercase;letter-spacing:.2px;white-space:nowrap}
.btn .arr{width:14px;height:14px;border-radius:50%;background:#fff;display:inline-block;position:relative}
.btn .arr::after{content:"";position:absolute;left:4px;top:4px;border-left:6px solid var(--blue);border-top:3px solid transparent;border-bottom:3px solid transparent}
.topline{top:0;left:0;width:1200px;height:9px;background:var(--blue)}
.brand{display:flex;align-items:center;gap:10px}
.brand .sq{width:60px;height:60px;background:var(--blue)}
.brand span{font-family:"Roboto",sans-serif;font-weight:700;font-size:16px;color:#111;line-height:20px;text-transform:uppercase}
.contact{display:flex;gap:12px;align-items:center;font-size:14px}
.contact b{display:block;font-family:"Roboto",sans-serif;font-weight:500;font-size:13px;color:#222}
.nav{top:105px;left:0;width:1200px;height:55px;background:var(--blue)}
.nav ul{list-style:none;display:flex;position:absolute;left:60px;top:0;height:55px;align-items:center}
.nav li{color:#fff;font-weight:700;font-size:15px;margin-right:40px;white-space:nowrap}
.search{position:absolute;right:14px;top:7px;width:240px;height:40px;background:var(--blue-dark);color:#fff;font-size:15px;padding:11px 28px;font-family:"Roboto",sans-serif}
.search i{position:absolute;right:0;top:0;width:40px;height:40px;background:#1a72c9}
.hero{top:160px;left:0;width:1200px;height:613px;background:radial-gradient(ellipse at 50% 55%,#1e5d8c 0%,#0b2b52 45%,#050f22 100%)}
.hero h1{color:#fff;font-size:52px;font-weight:700;top:145px}
.hero p{color:#fff;font-size:20px;top:238px}
.arrowbtn{width:36px;height:36px;border-radius:50%;background:var(--blue);top:237px}
.why{top:1175px;left:0;width:1200px;height:495px;background:linear-gradient(180deg,#1565b8,#0d5cad)}
.card{background:#fff;text-align:center}
.card .ic{width:90px;height:90px;margin:30px auto 0;background:#e4eef9;clip-path:polygon(25% 0,75% 0,100% 50%,75% 100%,25% 100%,0 50%)}
.card h3{font-size:17px;font-weight:700;color:#111;margin-top:28px;text-transform:uppercase}
.card p{font-size:15px;margin:12px 22px 0;line-height:22px;color:#333}
.testi{top:2148px;left:0;width:1200px;height:483px;background:linear-gradient(180deg,#0d5cad,#0b4e98)}
.tcard{background:#fff;text-align:center;padding-top:58px}
.tcard h4{font-family:"Roboto",sans-serif;color:var(--blue);font-size:15px;font-weight:700}
.tcard .r{font-size:15px;color:#333;margin-top:10px}
.tcard .l{font-size:14px;color:var(--muted);margin:16px 14px 0;line-height:18px}
.avatar{width:70px;height:70px;background:linear-gradient(#c9b8a8,#7a6a60);clip-path:polygon(50% 0,100% 25%,100% 75%,50% 100%,0 75%,0 25%)}
.svc{background:#fff;box-shadow:0 0 10px rgba(0,0,0,.12)}
.svc .ph{height:152px}
.svc h3{font-size:15px;font-weight:700;color:#111;margin:26px 0 0 50px}
.svc ul{list-style:none;margin:12px 0 0 50px}
.svc li{font-size:15px;color:#333;height:36px;display:flex;align-items:center;gap:10px}
.svc li::before{content:"";width:13px;height:13px;border-radius:50%;background:var(--blue)}
.svc .more{font-family:"Roboto",sans-serif;color:var(--blue);font-weight:700;font-size:15px;margin:4px 0 0 50px}
.foot{top:3656px;left:0;width:1200px;height:370px;background:var(--navy);color:#fff}
.foot h5{font-family:"Roboto",sans-serif;font-weight:400;font-size:17px;color:#3c86d6}
.foot li{list-style:none;font-size:15px;margin-top:15px}
</style>
</head>
<body>
<div class="abs topline"></div>
<header>
  <div class="abs brand" style="left:109px;top:26px"><div class="sq"></div><span>Ledgerwise<br>Forge</span></div>
  <div class="abs contact" style="left:617px;top:33px">
    <svg width="36" height="36" viewBox="0 0 36 36"><circle cx="18" cy="18" r="16" fill="none" stroke="#0d5cad" stroke-width="2"/><path d="M12 10l4 0 2 5-3 2c1 3 3 5 6 6l2-3 5 2v4c-10 1-17-6-16-16z" fill="#0d5cad"/></svg>
    <div><b>Phone</b>123 (4567) 890</div>
  </div>
  <div class="abs contact" style="left:832px;top:33px">
    <svg width="36" height="36" viewBox="0 0 36 36"><rect x="3" y="8" width="30" height="22" fill="none" stroke="#0d5cad" stroke-width="2"/><path d="M3 8l15 12 15-12" fill="none" stroke="#0d5cad" stroke-width="2"/></svg>
    <div><b>Email</b>info@ledgerwiseforge.com</div>
  </div>
</header>
<nav class="abs nav">
  <ul><li>Home</li><li>Services</li><li>About Us</li><li>Ledgerwise Forge Method</li><li>Testimonials</li><li>Blog</li><li>Contact Us</li></ul>
  <svg class="abs" style="left:920px;top:0" width="30" height="55"><polygon points="18,0 28,0 10,55 0,55" fill="#fff"/></svg>
  <div class="search">Search<i></i></div>
</nav>

<section class="abs hero" role="img" aria-label="Man standing over a glowing city skyline with network lines">
  <h1 class="abs center">LEDGERWISE FORGE</h1>
  <p class="abs center">Your own cryptocurrency. Secure, easy to use, and built by an expert team.</p>
  <div class="abs arrowbtn" style="left:28px"></div>
  <div class="abs arrowbtn" style="left:1130px"></div>
  <div class="abs" style="left:372px;top:307px"><span class="btn">Get Stared <i class="arr"></i></span></div>
  <div class="abs" style="left:541px;top:307px"><span class="btn" style="font-size:14px">Schedule Free Consultation <i class="arr"></i></span></div>
  <svg class="abs" style="left:0;top:520px" width="1200" height="93"><polygon points="0,0 600,93 0,93" fill="#fff"/><polygon points="1200,0 600,93 1200,93" fill="#fff"/><polyline points="0,6 600,87 1200,6" fill="none" stroke="#0d5cad" stroke-width="10"/></svg>
</section>

<section>
  <h2 class="abs center" style="top:850px;font-size:40px;font-weight:700;color:var(--ink)">WELCOME TO<div class="bar"></div></h2>
  <p class="abs" style="left:250px;width:700px;top:932px;text-align:center;font-size:15px;line-height:26px">Ledgerwise Forge adds professionalism to cryptocurrency development. Our done-for-you service covers everything from development and IT operations to ongoing support. You have access to a full team, for less than the typical cost of a single developer.</p>
  <div class="abs" style="left:520px;top:1041px"><span class="btn">Learn More <i class="arr"></i></span></div>
</section>

<section class="abs why">
  <h2 class="abs center" style="top:58px;font-size:40px;font-weight:700;color:#fff">WHY CHOOSE LEDGERWISE FORGE<div class="bar" style="background:#fff"></div></h2>
  <div class="abs card" style="left:167px;top:180px;width:264px;height:247px"><div class="ic"></div><h3>Value</h3><p>A team of experts, regular updates, and fixed costs</p></div>
  <div class="abs card" style="left:467px;top:180px;width:264px;height:247px"><div class="ic"></div><h3>Support</h3><p>Receive advice and other services, beyond development.</p></div>
  <div class="abs card" style="left:767px;top:180px;width:264px;height:247px"><div class="ic"></div><h3>Commitment</h3><p>Enjoy regular updates and new features.</p></div>
</section>

<section>
  <svg class="abs" style="left:125px;top:1747px" width="344" height="331" role="img" aria-label="Person analysing a trading chart on a monitor"><defs><linearGradient id="g1" x1="0" y1="0" x2="1" y2="1"><stop offset="0" stop-color="#5c6470"/><stop offset="1" stop-color="#d8d8d8"/></linearGradient></defs><polygon points="80,5 285,12 340,185 170,325 5,190" fill="url(#g1)" stroke="#e8eef6" stroke-width="6"/><polygon points="80,5 285,12 340,185 170,325 5,190" fill="none" stroke="#0d5cad" stroke-width="2"/></svg>
  <h2 class="abs" style="left:561px;top:1757px;font-size:40px;font-weight:700;color:var(--ink)">ABOUT US</h2>
  <p class="abs" style="left:561px;top:1836px;width:520px;font-size:15px;line-height:30px">In addition to creating and enhancing cryptocurrencies for clients, the Ledgerwise Forge team has been running the Quillcoin cryptocurrency since 2017. We prefer long-term relationships, enabling us to deliver the very highest quality and giving you peace of mind that you've got a professional and trustworthy team at your side.</p>
  <div class="abs" style="left:561px;top:2017px"><span class="btn">Learn More <i class="arr"></i></span></div>
</section>

<section class="abs testi">
  <h2 class="abs center" style="top:40px;font-size:40px;font-weight:700;color:#fff">CLIENT TESTIMONIALS<div class="bar" style="background:#fff"></div></h2>
  <div class="abs tcard" style="left:162px;top:215px;width:241px;height:192px"><h4>Mara Delune</h4><div class="r">Lorem ipsum dolor amet</div><div class="l">Lorem ipsum consectetur adipiscing elit, sed do eiusmod tempor labore dolore magna.</div></div>
  <div class="abs tcard" style="left:452px;top:196px;width:295px;height:236px"><h4 style="font-size:16px">Wendel Orsk</h4><div class="r">Lorem ipsum dolor amet</div><div class="l" style="margin:16px 24px 0;font-size:15px;line-height:21px">Lorem ipsum dolor consectetur adipiscing elit, sed do eiusmod tempor incididunt ut labore dolore magna aliqua.</div></div>
  <div class="abs tcard" style="left:797px;top:215px;width:239px;height:192px"><h4>Jory Palm</h4><div class="r">Lorem ipsum dolor amet</div><div class="l">Lorem ipsum consectetur adipiscing elit, sed do eiusmod tempor labore dolore magna.</div></div>
  <div class="abs avatar" role="img" aria-label="Client portrait" style="left:248px;top:180px"></div>
  <div class="abs avatar" role="img" aria-label="Client portrait" style="left:555px;top:155px;width:88px;height:88px"></div>
  <div class="abs avatar" role="img" aria-label="Client portrait" style="left:882px;top:180px"></div>
</section>

<section>
  <h2 class="abs center" style="top:2704px;font-size:40px;font-weight:700;color:var(--ink)">OUR SERVICES<div class="bar"></div></h2>
  <div class="abs svc" style="left:111px;top:2817px;width:298px;height:356px">
    <div class="ph" role="img" aria-label="Hands holding a tablet with coin graphics" style="background:linear-gradient(135deg,#3a3a3a,#c46a3a,#e8d8c8)"></div>
    <h3>BASIC OFFERING</h3><ul><li>Lower cost per month</li><li>Slower release schedule</li><li>Limited support hours</li></ul><div class="more">Read More ›</div></div>
  <div class="abs svc" style="left:450px;top:2817px;width:298px;height:356px">
    <div class="ph" role="img" aria-label="Glowing coin symbol on a monitor in a dark room" style="background:linear-gradient(135deg,#1b1b1b,#1f4f7a,#0a0a0a)"></div>
    <h3 style="margin-left:33px">FULL SERVICE OFFERING</h3><ul style="margin-left:33px"><li>Mid-range cost per month</li><li>Releases every 1.5 - 2 months</li><li>Client can help request</li></ul><div class="more" style="margin-left:33px">Read More ›</div></div>
  <div class="abs svc" style="left:791px;top:2817px;width:298px;height:356px">
    <div class="ph" role="img" aria-label="Man checking a phone next to a laptop chart" style="background:linear-gradient(135deg,#6a5a4a,#b9a58e,#3a3a3a)"></div>
    <h3 style="margin-left:34px">PREMIUM SERVICE</h3><ul style="margin-left:34px"><li>Higher cost per month</li><li>Priority 24/7 support</li><li>Dedicated development lead</li></ul><div class="more" style="margin-left:34px">Read More ›</div></div>
</section>

<section class="abs" style="top:3259px;left:0;width:1200px;height:420px;background:var(--light)">
  <h2 class="abs center" style="top:41px;font-size:40px;font-weight:700;color:var(--ink)">LOREM IPSUM DOLOR<div class="bar"></div></h2>
  <p class="abs" style="left:220px;width:760px;top:126px;text-align:center;font-size:15px;line-height:26px">Lorem ipsum dolor sit amet, consectetur adipiscing elit, sed do eiusmod tempor incididunt ut labore et dolore magna aliqua. Ut enim ad minim veniam, quis nostrud exercitation ullamco laboris nisi ut aliquip ex ea commodo consequat. Duis aute irure dolor in reprehenderit in voluptate velit esse cillum dolore fugiat nulla pariatur. Excepteur sint occaecat cupidatat non proident, sunt in culpa qui officia</p>
  <div class="abs" style="left:457px;top:260px"><span class="btn">Schedule Free Consultation <i class="arr"></i></span></div>
</section>

<footer class="abs foot">
  <svg class="abs" style="left:0;top:-60px" width="1200" height="80"><polygon points="0,62 600,2 1200,62 1200,80 0,80" fill="#07142b"/><polyline points="0,64 600,4 1200,64" fill="none" stroke="#0d5cad" stroke-width="8"/></svg>
  <div class="abs brand" style="left:109px;top:65px"><div class="sq"></div><span style="color:#fff">Ledgerwise<br>Forge</span></div>
  <p class="abs" style="left:109px;top:170px;width:240px;font-size:15px;line-height:24px">Ledgerwise Forge adds professionalism to cryptocurrency development.</p>
  <div class="abs" style="left:425px;top:78px"><h5>Quicklinks</h5><ul><li>Services</li><li>Ledgerwise Forge Method</li><li>Testimonials</li><li>Blog</li><li>About Us</li></ul></div>
  <div class="abs" style="left:705px;top:78px"><h5>Qtherlinks</h5><ul><li>blog</li><li>privacy</li><li>Services</li><li>Team</li></ul></div>
  <div class="abs" style="left:877px;top:78px"><h5 style="font-size:15px">Get our Newsletter</h5>
    <div style="margin-top:16px;width:208px;height:40px;background:#fff;color:#555;font-size:14px;padding:11px 12px">Enter News</div>
    <div class="btn" style="margin-top:16px;height:40px;font-size:15px;padding:0 24px">Subscribe</div>
    <div style="display:flex;gap:18px;margin-top:24px">
      <i style="width:9px;height:9px;border-radius:50%;background:#fff"></i><i style="width:9px;height:9px;border-radius:50%;background:#fff"></i><i style="width:9px;height:9px;border-radius:50%;background:#fff"></i><i style="width:9px;height:9px;border-radius:50%;background:#fff"></i><i style="width:9px;height:9px;border-radius:50%;background:#fff"></i></div>
  </div>
  <div class="abs" style="left:109px;top:305px;width:974px;height:1px;background:#2a3550"></div>
  <p class="abs center" style="top:327px;font-size:15px">©Copyrights 2021 &nbsp;Ledgerwise Forge &nbsp;| &nbsp;&nbsp;All Rights Reserved &nbsp;|</p>
</footer>
</body>
</html>
```